Moderne Visitenkarten für Medizintechnikfirma
Zielgruppe
Vertriebsfirma von moderner und innovativer Medizintechnik
Zielgruppe: Ärzte, Kliniken, Medizintechnikfirmen, Patienten
Aufgabenstellung
Besonderes, modernes, auffälliges und ansprechendes Design ohne überladen oder aufdringlich zu sein
Farbenorientierung kann am Logo und der Website geschehen. Wenn zum Logo harmonierend, sind aber auch andere Farben gerne gesehen.
Format: eher horizontal, vertikal aber auch möglich, abgerundete Ecken einplanen
Wenn möglich folgende Infos bitte schon auf die Karten bringen (pro Person eine Karte):
Konrad Faltermann (CEO)
konrad.faltermann@vitalis-partner.de
(Vitalis Partner GmbH
Lindenhof 12
26210 Grünstedt)
www.vitalis-partner.de
info@vitalis-partner.de
Jonas Prasken (CoS)
jonas.prasken@vitalis-partner.de
Die allgemeinen Firmeninfos können deutlich kleiner sein. Anschrift nur wenn es dadurch nicht zu viel werden würde.

```html
<!DOCTYPE html>
<html lang="de">
<head>
<meta charset="utf-8">
<title>Vitalis Partner – Visitenkarten</title>
<link rel="stylesheet" href="https://fonts.googleapis.com/css2?family=Montserrat:wght@400;500;600;700&display=swap">
<style>
  :root {
    --stage: #2a1f41;
    --card: #ffffff;
    --brand-purple: #4b3a7e;
    --brand-red: #e0381a;
    --tagline-grey: #7d7d7d;
    --network-tint: #d9d5e6;
  }
  * { box-sizing: border-box; margin: 0; padding: 0; }
  html, body { width: 1200px; height: 1200px; overflow: hidden; }
  body {
    background: var(--stage);
    font-family: "Montserrat", sans-serif;
    position: relative;
  }
  .card {
    position: absolute;
    left: 304px;
    width: 592px;
    height: 383px;
    background: var(--card);
    border-radius: 38px;
    overflow: hidden;
  }
  .card--front { top: 194px; }
  .card--back { top: 669px; }

  .network-field { position: absolute; }
  .card--front .network-field {
    left: 0; right: 0; bottom: 0; height: 200px;
    background: linear-gradient(to bottom, rgba(217,213,230,0) 0%, rgba(217,213,230,0.35) 100%);
  }
  .card--back .network-field {
    right: 0; top: 0; width: 200px; height: 180px;
    background: radial-gradient(ellipse at top right, rgba(217,213,230,0.45) 0%, rgba(217,213,230,0) 70%);
  }

  .brand-mark {
    position: absolute;
    border-radius: 50%;
    background: var(--brand-purple);
  }
  .card--front .brand-mark { left: 266px; top: 84px; width: 60px; height: 60px; }

  .brand-name {
    position: absolute;
    left: 0; right: 0;
    top: 210px;
    text-align: center;
    color: var(--brand-purple);
    font-weight: 600;
    font-size: 40px;
    line-height: 1;
    letter-spacing: -0.3px;
  }
  .brand-tagline {
    position: absolute;
    left: 0; right: 0;
    top: 257px;
    text-align: center;
    color: var(--tagline-grey);
    font-weight: 400;
    font-size: 13.5px;
    letter-spacing: 0.8px;
  }

  .back-mark { position: absolute; left: 40px; top: 40px; width: 110px; text-align: center; }
  .back-mark .brand-mark { position: static; display: block; width: 56px; height: 56px; margin: 0 auto 8px; }
  .back-mark__name { color: var(--brand-purple); font-weight: 600; font-size: 11px; }

  .person { position: absolute; left: 173px; top: 76px; color: var(--brand-purple); }
  .person__name { color: var(--brand-red); font-size: 21px; font-weight: 700; line-height: 1.2; }
  .person__role { font-weight: 400; }
  .person__line { font-size: 16px; font-weight: 500; line-height: 1.3; }

  .company { position: absolute; left: 45px; top: 285px; color: var(--brand-purple); font-size: 16px; line-height: 1.36; }
  .company__name { font-weight: 700; }
  .company__line { font-weight: 400; }

  .web { position: absolute; left: 339px; top: 303px; color: var(--brand-purple); font-size: 16px; line-height: 1.36; }
</style>
</head>
<body>
  <section class="card card--front">
    <div class="network-field" role="img" aria-label="Dezentes Netzwerkmuster aus Punkten und Linien"></div>
    <span class="brand-mark"></span>
    <div class="brand-name">Vitalis Partner</div>
    <div class="brand-tagline">MEDICAL TECHNOLOGY WITH PURPOSE</div>
  </section>

  <section class="card card--back">
    <div class="network-field" role="img" aria-label="Dezentes Netzwerkmuster aus Punkten und Linien"></div>
    <div class="back-mark">
      <span class="brand-mark"></span>
      <span class="back-mark__name">Vitalis Partner</span>
    </div>
    <div class="person">
      <div class="person__name">Konrad Faltermann <span class="person__role">(CEO)</span></div>
      <div class="person__line">+4915203847726</div>
      <div class="person__line">konrad.faltermann@vitalis-partner.de</div>
    </div>
    <div class="company">
      <div class="company__name">Vitalis Partner GmbH</div>
      <div class="company__line">Lindenhof 12 · 26210 Grünstedt</div>
      <div class="company__line">0800-5519036</div>
    </div>
    <div class="web">
      <div>info@vitalis-partner.de</div>
      <div>www.vitalis-partner.de</div>
    </div>
  </section>
</body>
</html>
```